Forensic Document Examiner, looking for contemporary update to my stationery design.

Looking for professional, classy logo design for stationery and business cards. My current stationery and business card is attached.I believe a logo image makes a header section interesting, so an intriguing design of a pen, feathered pen, microscope, magnifying glass, etc., would be appropriate. I have been in the business for over 30 years. I leave ideas to the imagination of the designer.My work involves mainly, the comparison of signatures and handwriting. I also resolve alterations, obliterations, and work as shown on my website: www.documentexaminer.infoThe image produced will be printed on quality white stationery and envelopes. The stationery will be photocopied by my clients, so the images should be reproducible. The business cards may be designed in other than white.

Target Market(s)

Attorneys

Font styles to use
Sans Serif

Colors

Designer to choose colors to be used in the design.

Requirements
Must have
• Image suitable for white stationery and photocopying.
• Classy logo and image; no casual fonts.
Nice to have
• Intriguing, contemporary design incorporating a relevant logo to my work.

```html
<!DOCTYPE html>
<html lang="en">
<head>
<meta charset="utf-8">
<title>Martin R. Hale Stationery</title>
<link rel="stylesheet" href="https://fonts.googleapis.com/css2?family=Didact+Gothic&family=Cabin+Condensed:wght@500&display=swap">
<style>
:root{
  --backdrop:#dcdcdc;
  --paper:#f7f7f6;
  --ink:#4a4a4a;
  --brand:#2e2f9a;
  --accent:#e0b400;
  --rule:#3a3a3a;
  --sig:#c9c9cc;
}
*{margin:0;padding:0;box-sizing:border-box}
html,body{width:1200px;height:877px;overflow:hidden;background:var(--backdrop)}
body{position:relative;font-family:"Didact Gothic",sans-serif;color:var(--ink)}
.sheet{position:absolute;background:var(--paper);box-shadow:0 1px 3px rgba(0,0,0,.12)}
.letterhead{left:59px;top:66px;width:527px;height:742px}
.envelope-back{left:620px;top:293px;width:530px;height:239px}
.envelope-front{left:620px;top:566px;width:532px;height:242px}
.brand{position:absolute;display:flex;align-items:flex-start;gap:6px}
.brand-mark{width:14px;height:14px;border-radius:50%;background:var(--brand);margin-top:6px}
.brand-name{color:var(--brand);line-height:1;letter-spacing:1px}
.brand-name .first{display:block;font-size:15px}
.brand-name .last{display:block;font-size:25px;letter-spacing:3px}
.brand-tagline{display:block;font-family:"Cabin Condensed",sans-serif;font-weight:500;color:var(--accent);font-size:8px;margin-top:2px;letter-spacing:0}
.letterhead .brand{left:45px;top:42px}
.contact{position:absolute;right:45px;top:45px;font-size:8px;text-align:right;line-height:10.8px}
.contact li{list-style:none;display:flex;justify-content:flex-end;align-items:center;gap:5px}
.contact svg{width:7px;height:7px;fill:var(--brand)}
.contact .noicon{padding-right:12px}
.salutation{position:absolute;left:45px;top:207px;font-size:13px}
.body-copy{position:absolute;left:45px;top:246px;width:438px;font-size:7.4px;line-height:11.4px;text-align:justify}
.body-copy p{margin-bottom:11.4px}
.closing{position:absolute;left:45px;top:484px;font-size:7.6px}
.signature{position:absolute;left:45px;top:506px;width:61px;height:26px;background:linear-gradient(90deg,var(--sig),#e6e6e8);border-radius:3px}
.footer{position:absolute;display:flex;align-items:center;font-size:8px}
.footer .rule{flex:1;height:1px;background:var(--rule);margin-right:2px}
.letterhead .footer{left:45px;right:44px;top:703px}
.envelope-front .footer{left:34px;right:32px;top:202px}
.flap{position:absolute;left:14px;right:14px;top:0;height:71px;border:1px solid #e4e4e4;border-top:none;border-radius:0 0 22px 22px}
.flap-mark{position:absolute;left:50%;top:30px;width:14px;height:14px;margin-left:-7px;border-radius:50%;background:var(--brand)}
.envelope-front .brand{left:32px;top:26px}
.envelope-front .brand-name .first{font-size:14px}
.envelope-front .brand-name .last{font-size:23px}
.return-address{position:absolute;left:39px;top:73px;font-size:8px}
</style>
</head>
<body>

<section class="sheet letterhead">
  <div class="brand">
    <span class="brand-mark"></span>
    <div class="brand-name"><span class="first">MARTIN R.</span><span class="last">HALE</span><span class="brand-tagline">Forensic Document Examiner</span></div>
  </div>
  <ul class="contact">
    <li>(555) 201-0147 <svg viewBox="0 0 10 10"><path d="M2 0l2 2-1 2c1 1 2 2 3 3l2-1 2 2-2 2C4 10 0 6 0 2z"/></svg></li>
    <li>mhale@quillmarkreview.info <svg viewBox="0 0 10 10"><path d="M0 2h10v6H0z M0 2l5 3 5-3" /></svg></li>
    <li>P.O.Box 2180, Lakeside <svg viewBox="0 0 10 10"><path d="M5 0a3.5 3.5 0 0 1 3.5 3.5C8.5 6 5 10 5 10S1.5 6 1.5 3.5A3.5 3.5 0 0 1 5 0zm0 2a1.5 1.5 0 1 0 0 3 1.5 1.5 0 0 0 0-3z"/></svg></li>
    <li class="noicon">OR 97001</li>
  </ul>
  <p class="salutation">Dear Mr. Carter,</p>
  <div class="body-copy">
    <p>Lorem ipsum dolor sit amet, consectetur adipiscing elit. Donec orci purus, luctus vitae dignissim eu, iaculis sed purus. Vivamus faucibus, ipsum nec aliquet viverra, leo mauris condimentum ligula, sit amet sagittis enim ligula quis arcu. Nam egestas tortor id nisi porttitor mattis. In tortor ante, ultricies in suscipit a, tempus non massa. Vivamus et auctor mi. Fusce vel massa nulla. Phasellus nec eros mauris, et scelerisque orci.</p>
    <p>Donec malesuada orci vitae nulla accumsan porta a id massa. Quisque accumsan iaculis magna sit amet fringilla. Maecenas consequat, magna eget tincidunt semper, odio nibh rutrum mi, id feugiat ante nisi eu risus. Vestibulum nunc orci, rhoncus a placerat in, ultricies in mi. Cras mattis varius eros, vel fringilla nisi suscipit eget. Quisque scelerisque sagittis nulla at porttitor.</p>
    <p>Sed id augue vitae urna euismod commodo aliquet a quam. Pellentesque arcu velit, cursus et malesuada ut, consequat et diam. Nullam erat sem, rhoncus id ullamcorper vitae, rhoncus et arcu. In ultricies ultricies nulla, ut rutrum nisi iaculis at. Donec eu magna a metus ornare faucibus. Fusce aliquet faucibus ultricies. Morbi semper, est id tincidunt gravida, sem arcu adipiscing lacus, ac bibendum nulla leo eu purus. Quisque nec diam sed risus consectetur accumsan quis quis nibh. Vestibulum id purus lorem.</p>
    <p>It is a long established fact that a reader will be distracted by the readable content of a page when looking at its layout. The point of using Lorem Ipsum is that it has a more-or-less normal distribution of letters, as opposed to using 'Content here, content here', making it look like readable English. Many desktop publishing packages</p>
  </div>
  <p class="closing">Sincerely,</p>
  <div class="signature" role="img" aria-label="Handwritten signature"></div>
  <div class="footer"><span class="rule"></span><span>www.quillmarkreview.info</span></div>
</section>

<section class="sheet envelope-back">
  <div class="flap"></div>
  <span class="flap-mark"></span>
</section>

<section class="sheet envelope-front">
  <div class="brand">
    <span class="brand-mark"></span>
    <div class="brand-name"><span class="first">MARTIN R.</span><span class="last">HALE</span><span class="brand-tagline">Forensic Document Examiner</span></div>
  </div>
  <p class="return-address">P.O.Box 2180, Lakeside, OR 97001</p>
  <div class="footer"><span class="rule"></span><span>www.quillmarkreview.info</span></div>
</section>

</body>
</html>
```